Heritage Hollow Business Cards

Require a business card design. <br/><br/>Needs to include logo (either round or long version) plus these details:<br/>Maya Torvell<br/>Heritage Hollow<br/>maya@kelvadtrading.com.au<br/>02 6481 7395<br/>PO Box Glenwarra NSW 2791<br/>www.heritagehollow.com.au<br/><br/>I need in an editable format so that I can create for multiple staff members. <br/><br/>

Target Market(s)

We are an online store selling renovation products to home owners are builders. Looking for a classic classy design.

Industry/Entity Type

Home And Garden

Contact Information for Business Card

Maya Torvell
Heritage Hollow
maya@kelvadtrading.com.au
02 6481 7395
PO Box Glenwarra NSW 2791
www.heritagehollow.com.au

Colors

Designer to choose colors to be used in the design.

Requirements
Must have
• Must include Logo.

```html
<!DOCTYPE html>
<html lang="en">
<head>
<meta charset="utf-8">
<title>Heritage Hollow Business Cards</title>
<link href="https://fonts.googleapis.com/css2?family=Raleway:ital,wght@0,400;0,500;1,400&display=swap" rel="stylesheet">
<style>
  :root {
    --page: #ffffff;
    --card-dark: #2d2b2a;
    --card-light: #ffffff;
    --card-edge: #bdbdbd;
    --ink: #2f2f2f;
    --ink-soft: #3a3a3a;
    --on-dark: #ececec;
  }
  html, body {
    margin: 0;
    padding: 0;
    width: 1200px;
    height: 923px;
    overflow: hidden;
    background: var(--page);
    font-family: "Raleway", Arial, sans-serif;
  }
  .canvas {
    position: relative;
    width: 1200px;
    height: 923px;
  }
  .card {
    position: absolute;
    width: 527px;
    height: 309px;
    box-sizing: border-box;
    border: 2px solid var(--card-edge);
  }
  .card--back {
    left: 486px;
    top: 195px;
    background: var(--card-dark);
  }
  .card--front {
    left: 252px;
    top: 459px;
    height: 310px;
    background: var(--card-light);
  }
  .brand-name {
    position: absolute;
    font-weight: 500;
    font-size: 27px;
    line-height: 1;
    letter-spacing: 0.5px;
    white-space: nowrap;
    transform: translate(-50%, -50%);
  }
  .card--back .brand-name {
    left: 50%;
    top: 50%;
    color: var(--on-dark);
  }
  .card--front .brand-name {
    left: 145px;
    top: 153px;
    color: var(--ink);
  }
  .holder {
    position: absolute;
    left: 345px;
    top: 62px;
    color: var(--ink);
  }
  .holder__name {
    margin: 0;
    font-weight: 400;
    font-size: 22px;
    letter-spacing: 0.6px;
    text-transform: uppercase;
    line-height: 1.1;
  }
  .holder__company {
    margin: 2px 0 0;
    font-style: italic;
    font-size: 14.5px;
    line-height: 1.2;
  }
  .contact {
    position: absolute;
    right: 29px;
    top: 213px;
    margin: 0;
    padding: 0;
    list-style: none;
    text-align: right;
    color: var(--ink-soft);
    font-size: 15.5px;
    line-height: 18.5px;
  }
</style>
</head>
<body>
  <main class="canvas">
    <section class="card card--back" aria-label="Card back">
      <div class="brand-name">Heritage Hollow</div>
    </section>

    <section class="card card--front" aria-label="Card front">
      <div class="brand-name">Heritage Hollow</div>
      <div class="holder">
        <h1 class="holder__name">Maya Torvell</h1>
        <p class="holder__company">Heritage Hollow</p>
      </div>
      <ul class="contact">
        <li>maya@kelvadtrading.com.au</li>
        <li>02 6481 7395</li>
        <li>PO Box Glenwarra NSW 2791</li>
        <li>www.heritagehollow.com.au</li>
      </ul>
    </section>
  </main>
</body>
</html>
```